Website for my photography business

I need a website for my photography business, Bram Kellet Photography. I need a website that has a landing page with a cover photo of each kind of photography I do. For example, Nature, Weddings, Portraits and Architecture. I want it so that when someone comes onto my website they have to choose which kind of photography page they want to visit. So if they click on the wedding photo it will open to a page with my wedding portfolio images and a contact me button. If they choose nature photography I want them to be redirected to an e-commerce section where they can purchase prints. Architecture and Portraits should open up to their respective portfolios with about me and contact info. I like this kind of format because I want people who come to my website for a specific type of photography to be able to be directed there easily without having to look at a mix of other kinds of photography. I will provide a few files to use as placeholders. I have already purchased the bramkelletphotography.example domain name. A Wix website would be great because I am most familiar with it but I am open to anything.

Industry/Entity Type

Photographer

Number of Pages Required

5+ page

Requirements
Must have
• Landing Page and e-commerce

```html
<!DOCTYPE html>
<html lang="en">
<head>
<meta charset="utf-8">
<title>Bram Kellet Photography</title>
<link rel="stylesheet" href="https://fonts.googleapis.com/css2?family=Montserrat:wght@300;400&family=Open+Sans:wght@400&display=swap">
<style>
  :root {
    --navy: #141b45;
    --yellow: #fbc324;
    --nav-grey: #9c9c9c;
    --rule: #d4d4dc;
    --ink: #333333;
    --white: #ffffff;
  }
  * { box-sizing: border-box; margin: 0; padding: 0; }
  html, body { width: 1200px; height: 932px; overflow: hidden; background: var(--white); }
  .page { position: relative; width: 1200px; height: 932px; font-family: "Montserrat", sans-serif; }

  .brand {
    position: absolute; left: 60px; top: 38px;
    font-family: "Montserrat", sans-serif; font-weight: 400; font-size: 24px;
    color: var(--navy); letter-spacing: 0.2px;
  }
  .deco-lines { position: absolute; left: 0; top: 0; width: 1200px; height: 932px; pointer-events: none; }

  .main-nav { position: absolute; top: 42px; left: 0; width: 1200px; }
  .main-nav a {
    position: absolute; font-weight: 300; font-size: 17px; color: var(--nav-grey);
    text-decoration: none; letter-spacing: 0.3px;
  }
  .main-nav a.is-current { color: var(--navy); font-weight: 400; }

  .category { position: absolute; display: block; text-decoration: none; }
  .category-photo { position: absolute; display: block; }
  .category-label {
    position: absolute; display: flex; align-items: center;
    font-weight: 400; color: var(--white); white-space: nowrap;
  }
  .label-yellow { background: var(--yellow); }
  .label-navy { background: var(--navy); }

  .portraits-photo { left: 68px; top: 127px; width: 250px; height: 537px;
    background: linear-gradient(160deg, #8a8a8a 0%, #5c5c5c 45%, #2e2e2e 100%); }
  .portraits-label { left: 279px; top: 127px; width: 217px; height: 79px; padding-left: 20px; font-size: 38px; }

  .nature-photo { left: 339px; top: 228px; width: 249px; height: 539px;
    background: linear-gradient(180deg, #36402e 0%, #4a4a2c 35%, #c9692a 60%, #e8eaee 100%); }
  .nature-label { left: 464px; top: 686px; width: 240px; height: 81px; padding-left: 22px; font-size: 38px; }

  .wedding-photo { left: 610px; top: 154px; width: 249px; height: 477px;
    background: linear-gradient(180deg, #b7a79a 0%, #2a3044 35%, #8f8073 65%, #c4b8ab 100%); }
  .wedding-label { left: 671px; top: 362px; width: 188px; height: 80px; justify-content: center; font-size: 30px; }

  .architecture-photo { left: 880px; top: 127px; width: 250px; height: 514px;
    background: linear-gradient(90deg, #7d8a8c 0%, #a8553b 45%, #b35a3c 70%, #c9bfae 100%); }
  .architecture-label { left: 841px; top: 641px; width: 289px; height: 81px; padding-left: 36px; font-size: 35px; }

  .site-footer { font-family: "Open Sans", sans-serif; color: var(--ink); font-size: 15px; }
  .footer-email { position: absolute; left: 72px; top: 834px; }
  .footer-legal { position: absolute; left: 954px; top: 833px; line-height: 23px; }
  .social { position: absolute; top: 849px; left: 538px; display: flex; gap: 18px; }
  .social a { color: #111111; text-decoration: none; font-size: 15px; }
</style>
</head>
<body>
<div class="page">
  <svg class="deco-lines" viewBox="0 0 1200 932" aria-hidden="true">
    <g stroke="var(--rule)" stroke-width="1.5">
      <line x1="368" y1="98" x2="419" y2="8"/>
      <line x1="381" y1="92" x2="433" y2="2"/>
      <line x1="720" y1="913" x2="771" y2="823"/>
      <line x1="734" y1="906" x2="787" y2="817"/>
    </g>
  </svg>

  <header>
    <div class="brand">Bram Kellet Photography</div>
    <nav class="main-nav">
      <a class="is-current" href="#" style="left:584px">HOME</a>
      <a href="#" style="left:687px">ABOUT</a>
      <a href="#" style="left:797px">GALLERY</a>
      <a href="#" style="left:924px">SHOP</a>
      <a href="#" style="left:1023px">CONTACT</a>
    </nav>
  </header>

  <main>
    <a class="category" href="#portraits">
      <span class="category-photo portraits-photo" role="img" aria-label="Black and white close-up portrait study"></span>
      <span class="category-label label-yellow portraits-label">/ Portraits</span>
    </a>
    <a class="category" href="#nature">
      <span class="category-photo nature-photo" role="img" aria-label="Red fox sitting in snow beneath evergreen trees"></span>
      <span class="category-label label-navy nature-label">/ Nature</span>
    </a>
    <a class="category" href="#wedding">
      <span class="category-photo wedding-photo" role="img" aria-label="Wedding rings resting on speckled granite"></span>
      <span class="category-label label-yellow wedding-label">/ Wedding</span>
    </a>
    <a class="category" href="#architecture">
      <span class="category-photo architecture-photo" role="img" aria-label="Modern brick and glass building with lamp post"></span>
      <span class="category-label label-navy architecture-label">/ Architecture</span>
    </a>
  </main>

  <footer class="site-footer">
    <div class="footer-email">info@companyname.com</div>
    <div class="social">
      <a href="#">Follow</a>
      <a href="#">Share</a>
    </div>
    <div class="footer-legal">© 2020 Company Name<br>All Rights Reserved</div>
  </footer>
</div>
</body>
</html>
```